Torvadex needs a website to buy and sell phones and electronics

We need a website to buy and sell smartphones.
https://www.quicklorratrade.com/
http://www.bramblequayshop.co.uk/
http://tradeyourunit.halvestorndepot.com/
https://www.k9loopbacker.co.uk/
https://www.brolvenmartex.co.uk/we-buy/

I logged into plorna.com and went to their online store template. I iike their template on the camera shop. I like the big letters but with elegance and formality. See link below:
http://www.plorna.com/website-template/view/html/1625?originUrl=http%3A%2F%2Fwww.plorna.com%2Fwebsite%2Ftemplates%2Fhtml%2Fonline-store%2F2&bookName=&galleryDocIndex=0&category=online-store

We know that these websites are too much work but we only need the landing page, without the that big search box. We want the various qavrixes such Qavrixes 4, 5, 6 and 7 and Turnwell Orbit S3, S4, S5 and S6 be listed with corresponding prices in Philippine currency.

We don't have a logo yet.

Notes To Designers: I would like to have a good feel of the site and I hope these sites can give you a feel. - quicklorratrade.com - bramblequayshop.co.uk Note: Please read the brief for updates. Also: i paid for the coded website so I believe it must be a running website. Thank you.

Target Market(s)

Philippines

Industry/Entity Type

Electronics

Coding

Coded - Design and coding required

Number of Pages Required

5+ page

Requirements
Must have
• Must displays phones of Qavrixes and Turnwell (Only the latest models for the last 2-3 years) not old
• Lumtabs and Kordial as well
Nice to have
• Logo - we need logo
• I love the simplicity but elegance of https://www.quicklorratrade.com/

```html
<!DOCTYPE html>
<html lang="en">
<head>
<meta charset="utf-8">
<title>Torvadex – We Buy and Sell Smartphones</title>
<link rel="stylesheet" href="https://fonts.googleapis.com/css2?family=Oswald:wght@500;600&family=Open+Sans:wght@300;400;600;700&display=swap">
<style>
:root{
  --navy:#0d2a5a;
  --navy-dark:#0a2148;
  --blue:#1b8fd6;
  --orange:#f57c2b;
  --green:#3c9a3c;
  --band:#dce9ef;
  --footer:#eef0f4;
  --text:#333a45;
  --muted:#555d66;
  --white:#ffffff;
}
*{margin:0;padding:0;box-sizing:border-box}
html,body{width:1200px;height:2620px;overflow:hidden}
body{position:relative;background:var(--white);font-family:"Open Sans",Arial,sans-serif;color:var(--text)}

/* header */
.site-header{position:absolute;left:0;top:0;width:1200px;height:110px;background:var(--white);z-index:3}
.brand{position:absolute;left:98px;top:12px;width:206px;height:206px;border-radius:50%;background:var(--blue);border:8px solid var(--white);display:flex;flex-direction:column;align-items:center;justify-content:center;z-index:4}
.brand-dot{width:24px;height:24px;border-radius:4px;background:var(--white);margin-bottom:12px}
.brand-name{font-family:"Open Sans",Arial,sans-serif;font-weight:700;font-size:27px;color:var(--white);letter-spacing:.5px}
.main-nav{position:absolute;top:44px;left:0;width:1200px}
.main-nav a{position:absolute;font-size:15px;color:var(--navy);text-decoration:none}

/* hero */
.hero{position:absolute;left:0;top:110px;width:1200px;height:594px;overflow:hidden}
.hero-photo{position:absolute;inset:0;background:linear-gradient(110deg,#8c6a55 0%,#b88b6c 22%,#9a8a80 45%,#7f756f 65%,#a49488 85%,#6d625c 100%)}
.hero-shade{position:absolute;inset:0;background:rgba(40,30,30,.28)}
.hero-title{position:absolute;top:206px;width:1200px;text-align:center;font-family:"Oswald",Arial,sans-serif;font-weight:600;font-size:41px;color:var(--white);letter-spacing:.5px}
.hero-offer{position:absolute;top:272px;width:1200px;text-align:center;font-family:"Open Sans",Arial,sans-serif;font-weight:300;font-size:64px;color:var(--white);letter-spacing:2px;padding-left:40px}
.hero-offer b{font-weight:700}
.hero-arrow{position:absolute;top:272px}

/* section headings */
.section-title{position:absolute;width:1200px;text-align:center;font-family:"Oswald",Arial,sans-serif;font-weight:600;font-size:31px;color:var(--navy);letter-spacing:.5px}

/* benefits */
.benefit{position:absolute;top:853px;width:260px;text-align:center}
.benefit-icon{width:146px;height:146px;border-radius:50%;border:1px solid #eceff2;margin:0 auto;display:flex;align-items:center;justify-content:center}
.benefit-name{margin-top:22px;font-size:16px;font-weight:600;color:#222;letter-spacing:.3px}
.benefit-text{margin-top:12px;font-size:13px;line-height:19px;color:var(--muted);padding:0 18px}

/* trade-ins */
.trade-band{position:absolute;left:0;top:1184px;width:1200px;height:773px;background:var(--band)}
.phone{position:absolute;width:256px;text-align:center}
.phone-photo{width:80px;height:156px;margin:0 auto;border-radius:14px;background:linear-gradient(160deg,#3a3f46 0%,#15181c 55%,#2e3238 100%)}
.phone-photo.light{background:linear-gradient(160deg,#f4f4f4 0%,#d7d9dc 60%,#ececec 100%);border:1px solid #c9ccd0}
.phone-name{margin-top:12px;font-size:23px;color:#222;line-height:30px}
.phone-price{margin-top:2px;font-size:17px;font-weight:600;color:var(--navy);line-height:24px}
.quote-btn{display:block;width:157px;height:38px;margin:8px auto 0;background:var(--orange);color:var(--white);font-size:15px;font-weight:600;line-height:38px;letter-spacing:.5px;text-decoration:none}

/* reasons */
.reason{position:absolute;width:432px;padding-left:32px}
.reason svg{position:absolute;left:0;top:1px}
.reason h3{font-size:14px;font-weight:700;color:var(--navy);line-height:20px}
.reason p{font-size:12.5px;line-height:20px;color:#333}

/* footer */
.site-footer{position:absolute;left:0;top:2533px;width:1200px;height:87px;background:var(--footer)}
.copyright{position:absolute;left:100px;top:32px;font-size:14px;color:var(--navy)}
.social{position:absolute;left:820px;top:26px;display:flex;align-items:center;gap:8px;font-size:14px;color:var(--navy)}
.social .label{margin-right:4px}
.social .dot{width:34px;height:34px;border-radius:50%}
</style>
</head>
<body>

<header class="site-header">
  <div class="brand"><span class="brand-dot"></span><span class="brand-name">TORVADEX</span></div>
  <nav class="main-nav">
    <a href="#" style="left:748px">Search</a>
    <a href="#" style="left:838px">How it works</a>
    <a href="#" style="left:968px">FAQs</a>
    <a href="#" style="left:1048px">Contact</a>
  </nav>
</header>

<section class="hero">
  <div class="hero-photo" role="img" aria-label="Photo of a woman in sunglasses holding a white smartphone"></div>
  <div class="hero-shade"></div>
  <svg class="hero-arrow" style="left:32px" width="16" height="30" viewBox="0 0 16 30"><path d="M14 2 2 15l12 13" fill="none" stroke="rgba(255,255,255,.7)" stroke-width="2"/></svg>
  <svg class="hero-arrow" style="left:1144px" width="16" height="30" viewBox="0 0 16 30"><path d="M2 2l12 13L2 28" fill="none" stroke="rgba(255,255,255,.7)" stroke-width="2"/></svg>
  <h1 class="hero-title">WE BUY AND SELL SMARTPHONES</h1>
  <p class="hero-offer">OFFER <b>₱ 50</b></p>
</section>

<h2 class="section-title" style="top:760px">WHY BUY AND SELL SMARTPHONES?</h2>

<div class="benefit" style="left:66px">
  <div class="benefit-icon"><svg width="74" height="66" viewBox="0 0 74 66"><rect x="2" y="28" width="14" height="36" rx="2" fill="var(--blue)"/><path d="M22 30 38 6c4-5 11-2 10 4l-3 14h20c5 0 8 4 7 8l-6 28c-1 3-3 5-6 5H22z" fill="var(--blue)"/></svg></div>
  <div class="benefit-name">PRICE GUARANTEE</div>
  <p class="benefit-text">Excepteur sint occaecat cupidatat non proident, sunt in culpa qui officia deserunt mollit anim.</p>
</div>
<div class="benefit" style="left:338px">
  <div class="benefit-icon"><svg width="76" height="76" viewBox="0 0 76 76"><circle cx="32" cy="34" r="26" fill="none" stroke="var(--blue)" stroke-width="7"/><path d="M32 18v17h12" fill="none" stroke="var(--blue)" stroke-width="6"/><circle cx="55" cy="55" r="18" fill="var(--blue)" stroke="#fff" stroke-width="3"/><text x="55" y="63" text-anchor="middle" font-family="Open Sans,Arial,sans-serif" font-weight="700" font-size="22" fill="#fff">$</text></svg></div>
  <div class="benefit-name">FAST PAYMENT</div>
  <p class="benefit-text">Sed quia non numquam eius modi tempora incidunt ut labore et dolore magnam aliquam.</p>
</div>
<div class="benefit" style="left:600px">
  <div class="benefit-icon"><svg width="72" height="80" viewBox="0 0 72 80"><rect x="20" y="4" width="34" height="56" rx="5" transform="rotate(25 37 32)" fill="none" stroke="var(--blue)" stroke-width="6"/><path d="M6 48c6-4 12 0 16 6l8 10c4 5 12 6 18 2l10-8 4 14-14 8H24L4 62z" fill="var(--blue)"/></svg></div>
  <div class="benefit-name">WE TAKE ALL PHONES</div>
  <p class="benefit-text">Quis autem vel eum iure reprehend qui in ea voluptate velit esse quam nihil molestiae.</p>
</div>
<div class="benefit" style="left:871px">
  <div class="benefit-icon"><svg width="72" height="64" viewBox="0 0 72 64"><path d="M36 36C36 20 44 8 66 6c0 18-12 28-30 30z" fill="var(--blue)"/><path d="M34 34C32 22 24 14 8 14c0 14 10 22 26 20z" fill="var(--blue)"/><path d="M2 46c8-4 16-2 22 2h16c4 0 4 6 0 6H26h16l20-8c4-2 8 2 4 6L44 62H2z" fill="var(--blue)"/></svg></div>
  <div class="benefit-name">ENVIRONMENT FRIENDLY</div>
  <p class="benefit-text">At vero eos et accusamus et iusto odio dignissimos ducimus qui blanditiis maginum.</p>
</div>

<section class="trade-band">
  <h2 class="section-title" style="top:54px">POPULAR PHONE TRADE-INS</h2>

  <div class="phone" style="left:87px;top:149px"><div class="phone-photo light" role="img" aria-label="White Qavrixes 4 phone"></div><div class="phone-name">Qavrixes 4</div><div class="phone-price">₱ 2,500</div><a class="quote-btn" href="#">GET A QUOTE</a></div>
  <div class="phone" style="left:344px;top:149px"><div class="phone-photo" role="img" aria-label="Black Qavrixes 5 phone"></div><div class="phone-name">Qavrixes 5</div><div class="phone-price">₱ 4,000</div><a class="quote-btn" href="#">GET A QUOTE</a></div>
  <div class="phone" style="left:600px;top:149px"><div class="phone-photo light" role="img" aria-label="White Qavrixes 6 phone"></div><div class="phone-name">Qavrixes 6</div><div class="phone-price">₱ 7,500</div><a class="quote-btn" href="#">GET A QUOTE</a></div>
  <div class="phone" style="left:857px;top:149px"><div class="phone-photo" role="img" aria-label="Black Qavrixes 7 phone"></div><div class="phone-name">Qavrixes 7</div><div class="phone-price">₱ 12,000</div><a class="quote-btn" href="#">GET A QUOTE</a></div>

  <div class="phone" style="left:87px;top:441px"><div class="phone-photo" role="img" aria-label="Dark Turnwell Orbit S3 phone"></div><div class="phone-name">Turnwell Orbit S3</div><div class="phone-price">₱ 2,000</div><a class="quote-btn" href="#">GET A QUOTE</a></div>
  <div class="phone" style="left:344px;top:441px"><div class="phone-photo light" role="img" aria-label="White Turnwell Orbit S4 phone"></div><div class="phone-name">Turnwell Orbit S4</div><div class="phone-price">₱ 3,000</div><a class="quote-btn" href="#">GET A QUOTE</a></div>
  <div class="phone" style="left:600px;top:441px"><div class="phone-photo" role="img" aria-label="Black Turnwell Orbit S5 phone"></div><div class="phone-name">Turnwell Orbit S5</div><div class="phone-price">₱ 4,500</div><a class="quote-btn" href="#">GET A QUOTE</a></div>
  <div class="phone" style="left:857px;top:441px"><div class="phone-photo" role="img" aria-label="Dark Turnwell Orbit S6 phone"></div><div class="phone-name">Turnwell Orbit S6</div><div class="phone-price">₱ 6,500</div><a class="quote-btn" href="#">GET A QUOTE</a></div>
</section>

<h2 class="section-title" style="top:2014px">WHY SHOULD YOU BUY AND SELL YOUR PHONES</h2>

<div class="reason" style="left:150px;top:2110px"><svg width="20" height="18" viewBox="0 0 20 18"><path d="M2 9l6 6L18 3" fill="none" stroke="var(--green)" stroke-width="4"/></svg><h3>100% satisfaction guaranteed</h3><p>In the unlikely event you send us your phone and we believe it isn’t worth what you thought it was, we’ll return your phone for free.</p></div>
<div class="reason" style="left:150px;top:2189px"><svg width="20" height="18" viewBox="0 0 20 18"><path d="M2 9l6 6L18 3" fill="none" stroke="var(--green)" stroke-width="4"/></svg><h3>Immediate payment</h3><p>We process your payment on the same day that we receive your phone (assuming your phone is in as described condition of course!). If you have chosen to be paid by bank transfer you will receive this in 3-5 working days.</p></div>
<div class="reason" style="left:150px;top:2308px"><svg width="20" height="18" viewBox="0 0 20 18"><path d="M2 9l6 6L18 3" fill="none" stroke="var(--green)" stroke-width="4"/></svg><h3>No hidden surprises</h3><p>Unlike some other phone recyclers, our straightforward acceptance criteria means that we pay you what we say we will – so you won’t have to worry about any surprises or additional costs.</p></div>
<div class="reason" style="left:150px;top:2406px"><svg width="20" height="18" viewBox="0 0 20 18"><path d="M2 9l6 6L18 3" fill="none" stroke="var(--green)" stroke-width="4"/></svg><h3>Recycle any phone brand</h3><p>You can recycle any phone and any brand that that you own including Pomeli Qavrix, Turnwell, Kestro, Valtuna and Sorvane</p></div>

<div class="reason" style="left:655px;top:2110px"><svg width="20" height="18" viewBox="0 0 20 18"><path d="M2 9l6 6L18 3" fill="none" stroke="var(--green)" stroke-width="4"/></svg><h3>We take broken phones</h3><p>We even buy non-working or damaged (but intact) phones and can also recycle heavily damaged phones for you.</p></div>
<div class="reason" style="left:655px;top:2189px"><svg width="20" height="18" viewBox="0 0 20 18"><path d="M2 9l6 6L18 3" fill="none" stroke="var(--green)" stroke-width="4"/></svg><h3>Trade-in online or in-store</h3><p>Sell your phone to us online and we’ll send you a free postage pack. Or you can trade in your phone at any Halvestorn Depot store for instant payment.</p></div>
<div class="reason" style="left:655px;top:2289px"><svg width="20" height="18" viewBox="0 0 20 18"><path d="M2 9l6 6L18 3" fill="none" stroke="var(--green)" stroke-width="4"/></svg><h3>Environmentally friendly recycling</h3><p>We buy 1000s of phones every month and we’re committed to ensuring 100% of these are recycled in an environmentally friendly fashion.</p></div>
<div class="reason" style="left:655px;top:2387px"><svg width="20" height="18" viewBox="0 0 20 18"><path d="M2 9l6 6L18 3" fill="none" stroke="var(--green)" stroke-width="4"/></svg><h3>We trade-in phones from all networks</h3><p>We buy phones from all the major networks including Nexacell, Velocom and Brightline. And you don’t need to have bought your phone from Halvestorn Depot either.</p></div>

<footer class="site-footer">
  <p class="copyright">© 2017 Torvadex . All right reserved.&nbsp; Term of Use</p>
  <div class="social">
    <span class="label">Connect With Us:</span>
    <span class="dot" style="background:#3aa0d8"></span>
    <span class="dot" style="background:#2f5aa0"></span>
    <span class="dot" style="background:#1a74a8"></span>
    <span class="dot" style="background:#d4452f"></span>
  </div>
</footer>

</body>
</html>
```